Business card for a Exhibition booth fabrication company

Hi. My company would like to change our corporate name card. We are an events and Exhibition stand builder company. We would like our corporate name card to resonate what we do. I need someone to create something unique that relates to the industry that I am in. The graphic designer should be creative to incorporate the elements of my industry and try to blend in well in the design of the card. Our aim is to ensure that we are unique and our card can look different from our competitors.
Updates

Target Market(s)

Marketing and events manager from all companies

Contact Information for Business Card

The business card should have the following details:
Name
Job Title
Email
Website

Colors

Designer to choose colors to be used in the design.

Requirements
Must have
• The card must be look something that is relevant to the service that I am providing. My website is: www.velmora-buildworks.com
• You can see my website to get more information on what service that I am doing
Nice to have
• On the back of my card, I would like to have a globe image with the incorporation of my company logo. This is to indicate that my services can be done in any part of the world.

```html
<!DOCTYPE html>
<html lang="en">
<head>
<meta charset="utf-8">
<title>Velmora Buildworks – Business Card</title>
<link rel="stylesheet" href="https://fonts.googleapis.com/css2?family=Montserrat:wght@600;700&family=Roboto:wght@400;500;700&display=swap">
<style>
  :root {
    --page-bg: #e4e1de;
    --card-bg: #ffffff;
    --brand-red: #e8232a;
    --ink-dark: #4a4a4a;
    --ink-mid: #5f5f5f;
    --tab-grey: #606060;
    --rule-grey: #9a9a9a;
    --map-grey: #ececec;
  }
  * { box-sizing: border-box; margin: 0; padding: 0; }
  html, body { width: 1200px; height: 997px; overflow: hidden; }
  body {
    background: var(--page-bg);
    font-family: "Roboto", Arial, sans-serif;
    position: relative;
  }
  .card {
    position: absolute;
    left: 250px;
    width: 700px;
    height: 400px;
    background: var(--card-bg);
    box-shadow: 0 6px 18px rgba(0,0,0,0.12);
    overflow: hidden;
  }
  .card--front { top: 64px; }
  .card--back { top: 533px; }

  /* Brand lockup */
  .brand {
    position: absolute;
    display: flex;
    align-items: center;
    gap: 12px;
    font-family: "Montserrat", Arial, sans-serif;
    font-weight: 700;
    color: var(--ink-dark);
    letter-spacing: 3px;
    white-space: nowrap;
  }
  .brand__dot {
    border-radius: 50%;
    background: var(--brand-red);
    flex: none;
  }
  .card--front .brand { left: 48px; top: 62px; font-size: 19px; }
  .card--front .brand__dot { width: 40px; height: 40px; }

  /* Person + address */
  .person {
    position: absolute;
    right: 40px;
    top: 52px;
    text-align: right;
  }
  .person__name {
    color: var(--brand-red);
    font-weight: 700;
    font-size: 20px;
    letter-spacing: 0.3px;
  }
  .person__title {
    color: var(--ink-mid);
    font-size: 14px;
    border-top: 1px solid var(--rule-grey);
    display: inline-block;
    padding: 2px 0 0 40px;
    margin-top: 2px;
  }
  .address {
    position: absolute;
    right: 40px;
    top: 128px;
    text-align: right;
    color: var(--ink-dark);
    font-size: 15px;
    line-height: 1.35;
  }

  .divider {
    position: absolute;
    left: 48px;
    right: 40px;
    top: 225px;
    border-top: 1px solid var(--rule-grey);
  }

  /* Contacts */
  .contacts {
    position: absolute;
    left: 48px;
    top: 262px;
    list-style: none;
    color: var(--ink-dark);
    font-size: 15px;
    line-height: 1.6;
  }
  .contacts li { display: flex; align-items: center; gap: 8px; }
  .contacts svg { width: 13px; height: 13px; flex: none; }

  .footer-band {
    position: absolute;
    left: 0; bottom: 0;
    width: 700px; height: 120px;
  }

  /* Back */
  .world-map {
    position: absolute;
    left: 60px; top: 30px;
    width: 600px; height: 300px;
    border-radius: 40% 45% 35% 40%;
    background: radial-gradient(ellipse at center, var(--map-grey) 0%, var(--map-grey) 55%, rgba(236,236,236,0) 75%);
  }
  .card--back .brand {
    left: 50%; top: 50%;
    transform: translate(-50%, -50%);
    font-size: 24px;
    gap: 14px;
  }
  .card--back .brand__dot { width: 48px; height: 48px; }
</style>
</head>
<body>

<section class="card card--front" aria-label="Card front">
  <div class="brand"><span class="brand__dot"></span>VELMORA BUILDWORKS</div>

  <div class="person">
    <div class="person__name">DANIEL REYES</div>
    <div class="person__title">President</div>
  </div>

  <address class="address" style="font-style:normal">
    P.O. Box 4120, Al Rayyan,<br>Street Doha - Qatar
  </address>

  <div class="divider"></div>

  <ul class="contacts">
    <li>
      <svg viewBox="0 0 13 13" aria-hidden="true"><rect x="3" y="1" width="7" height="11" rx="1.5" fill="none" stroke="#e8232a" stroke-width="1.4"/><circle cx="6.5" cy="10" r="0.8" fill="#e8232a"/></svg>
      +974 5550 2187
    </li>
    <li>
      <svg viewBox="0 0 13 13" aria-hidden="true"><rect x="1" y="2.5" width="11" height="8" rx="1" fill="#e8232a"/><path d="M1.5 3.2 L6.5 7 L11.5 3.2" fill="none" stroke="#fff" stroke-width="1"/></svg>
      info@velmora-buildworks.com
    </li>
    <li>
      <svg viewBox="0 0 13 13" aria-hidden="true"><circle cx="6.5" cy="6.5" r="5.5" fill="#e8232a"/><path d="M1 6.5 H12 M6.5 1 C3.5 4 3.5 9 6.5 12 M6.5 1 C9.5 4 9.5 9 6.5 12" fill="none" stroke="#fff" stroke-width="0.8"/></svg>
      www.velmora-buildworks.com
    </li>
  </ul>

  <svg class="footer-band" viewBox="0 0 700 120" aria-hidden="true">
    <polygon points="360,82 395,20 700,20 700,82" fill="var(--tab-grey)"/>
    <rect x="0" y="108" width="700" height="7" fill="var(--brand-red)"/>
    <polygon points="360,108 380,82 700,82 700,108" fill="var(--tab-grey)"/>
  </svg>
</section>

<section class="card card--back" aria-label="Card back">
  <div class="world-map" role="img" aria-label="Faint grey world map in the background"></div>
  <div class="brand"><span class="brand__dot"></span>VELMORA BUILDWORKS</div>
</section>

</body>
</html>
```